Business Card Design for Marketing Firm

Looking for business card design for higher end marketing firm. Clean but impressionable/trendy. We are a marketing firm that represents manufacturers in the foodservice equipment and supply industry. Our customers are end users such has hotels, restaurants, country clubs, convention centers and casinos as well as distributors of restaurants supplies and equipment, and manufacturers of foodservice equipment and supplies.
Target Market(s)
Hotels, Restaurants, Supply & Equipment Distributors, Foodservice Manufacturers
Industry/Entity Type
Foodservice/Hospitality
Contact Information for Business Card
Name, Title, Contact Number, Email, Website, Social Media, Address
Requirements
Must have
- Clean & Simple but Serious and Impressionable

```html
<!DOCTYPE html>
<html lang="en">
<head>
<meta charset="utf-8">
<title>Meridian Service Reps – Business Card</title>
<link rel="stylesheet" href="https://fonts.googleapis.com/css2?family=Poppins:wght@400;600&display=swap">
<style>
  :root {
    --brand-blue: #0b0a8f;
    --paper: #ffffff;
    --backdrop: #e9e9ee;
    --ink-on-blue: #ffffff;
  }
  html, body {
    margin: 0;
    width: 1200px;
    height: 900px;
    overflow: hidden;
    background: var(--backdrop);
    font-family: "Poppins", sans-serif;
  }
  .canvas {
    position: relative;
    width: 1200px;
    height: 900px;
  }
  .card {
    position: absolute;
    left: 300px;
    width: 600px;
    height: 343px;
    box-shadow: 0 6px 18px rgba(0,0,0,0.18);
    overflow: hidden;
  }
  .card--front { top: 70px; background: var(--brand-blue); color: var(--ink-on-blue); }
  .card--back  { top: 470px; background: var(--paper); color: var(--brand-blue); }

  /* Brand lockup */
  .brand {
    position: absolute;
    display: flex;
    flex-direction: column;
    align-items: center;
  }
  .brand__dot {
    width: 46px;
    height: 46px;
    border-radius: 50%;
    border: 3px solid currentColor;
    margin-bottom: 14px;
  }
  .brand__name {
    font-weight: 400;
    letter-spacing: 0.12em;
    text-transform: uppercase;
    white-space: nowrap;
    padding-bottom: 6px;
    border-bottom: 2px solid currentColor;
  }
  .card--front .brand { left: 0; right: 0; top: 72px; }
  .card--front .brand__name { font-size: 24px; }
  .card--back .brand { left: 300px; width: 280px; top: 34px; }
  .card--back .brand__dot { width: 34px; height: 34px; margin-bottom: 10px; }
  .card--back .brand__name { font-size: 17px; }

  .social {
    position: absolute;
    left: 0; right: 0; top: 238px;
    display: flex;
    justify-content: center;
    gap: 10px;
  }
  .social__badge {
    width: 28px;
    height: 28px;
    border-radius: 50%;
    border: 2px solid var(--ink-on-blue);
  }

  /* Contact side */
  .person { position: absolute; left: 46px; top: 46px; }
  .person__name { margin: 0; font-size: 23px; font-weight: 600; letter-spacing: 0.02em; line-height: 1.1; }
  .person__title { margin: 2px 0 0; font-size: 15px; font-weight: 400; }

  .contact { position: absolute; left: 46px; top: 150px; font-size: 15px; line-height: 1.45; }
  .contact__row { display: flex; align-items: center; gap: 10px; }
  .contact__icon { width: 18px; height: 18px; fill: var(--brand-blue); flex: none; }
  .contact__address { margin: 10px 0 0 28px; font-style: normal; }

  .wave { position: absolute; inset: 0; }
  .website {
    position: absolute;
    right: 36px;
    bottom: 34px;
    font-size: 14px;
    color: var(--ink-on-blue);
    letter-spacing: 0.02em;
  }
</style>
</head>
<body>
<main class="canvas">

  <section class="card card--front" aria-label="Card front">
    <div class="brand">
      <span class="brand__dot"></span>
      <span class="brand__name">Meridian Service Reps</span>
    </div>
    <div class="social" aria-label="Social media">
      <span class="social__badge"></span>
      <span class="social__badge"></span>
      <span class="social__badge"></span>
    </div>
  </section>

  <section class="card card--back" aria-label="Card back">
    <svg class="wave" width="600" height="343" viewBox="0 0 600 343" aria-hidden="true">
      <path d="M0,300 C200,312 410,255 600,160 L600,343 L0,343 Z" fill="var(--brand-blue)"/>
      <path d="M0,322 C200,322 360,262 470,205" fill="none" stroke="var(--paper)" stroke-width="3"/>
    </svg>

    <div class="person">
      <h1 class="person__name">DANIEL MARSH</h1>
      <p class="person__title">Managing Director</p>
    </div>

    <div class="brand">
      <span class="brand__dot"></span>
      <span class="brand__name">Meridian Service Reps</span>
    </div>

    <div class="contact">
      <div class="contact__row">
        <svg class="contact__icon" viewBox="0 0 24 24" aria-hidden="true"><path d="M6.6 10.8a15.1 15.1 0 0 0 6.6 6.6l2.2-2.2c.3-.3.7-.4 1-.2 1.1.4 2.3.6 3.6.6.6 0 1 .4 1 1V20c0 .6-.4 1-1 1A17 17 0 0 1 3 4c0-.6.4-1 1-1h3.5c.6 0 1 .4 1 1 0 1.3.2 2.5.6 3.6.1.3 0 .7-.2 1z"/></svg>
        <span>055-318 602 417</span>
      </div>
      <div class="contact__row">
        <svg class="contact__icon" viewBox="0 0 24 24" aria-hidden="true"><path d="M2 5h20v14H2z M3.5 6.5 12 13l8.5-6.5" fill="none" stroke="var(--brand-blue)" stroke-width="2"/></svg>
        <span>hello@meridianreps.com</span>
      </div>
      <address class="contact__address">18 Harbour Row, Suite 4<br>Eastbrook, 30918</address>
    </div>

    <span class="website">www.meridianreps.com</span>
  </section>

</main>
</body>
</html>
```